Copperleaf Roofing Business Card

This is my current business card. But I’d like to make some changes. Somewhere on the card I’d like to list some of the services we offer. Maybe on the back? But I’d still like to keep the red. White and black modern look.

-residential & commercial roofing
-Roof Repairs & Maintenance
-Storm Damage & Insurance Claims specialist
-Christmas Lights and permanent Christmas lights
Fencing. Windows. Gutters. Siding. Sheetrock, painting.

```html
<!DOCTYPE html>
<html lang="en">
<head>
<meta charset="utf-8">
<title>Copperleaf Roofing Business Card</title>
<link href="https://fonts.googleapis.com/css2?family=Poppins:wght@400;500;700;800&display=swap" rel="stylesheet">
<style>
  :root {
    --bg: #2a2a2a;
    --black: #111111;
    --black-soft: #1c1c1c;
    --emboss: #171717;
    --white: #ffffff;
    --red: #e01b1b;
    --red-dark: #a80f12;
    --ink: #1a1a1a;
  }
  * { box-sizing: border-box; margin: 0; padding: 0; }
  html, body { width: 1200px; height: 689px; overflow: hidden; }
  body {
    background: var(--bg);
    font-family: "Poppins", sans-serif;
    position: relative;
  }
  .card {
    position: absolute;
    top: 190px;
    width: 550px;
    height: 310px;
    border-radius: 18px;
    overflow: hidden;
  }

  /* Back of card */
  .card-back { left: 35px; background: linear-gradient(135deg, var(--black-soft), var(--black)); }
  .back-mark {
    position: absolute; right: 36px; top: 22px; width: 190px; height: 190px;
    border-radius: 50%;
    background: radial-gradient(circle at 40% 35%, #1e1e1e, var(--emboss));
    box-shadow: inset 0 0 0 1px #222;
  }
  .extras {
    position: absolute; left: 36px; top: 28px;
    list-style: none; color: var(--white); font-size: 14px; line-height: 21px;
  }
  .services {
    position: absolute; left: 36px; top: 180px;
    list-style: none; color: var(--white); font-size: 14px; line-height: 24px;
  }
  .extras li, .services li { display: flex; align-items: center; gap: 10px; white-space: nowrap; }
  .bullet {
    width: 10px; height: 10px; border: 1.5px solid var(--red);
    transform: rotate(45deg); display: inline-block; position: relative; flex: none;
  }
  .bullet::after { content: ""; position: absolute; inset: 2px; background: var(--red); }

  /* Front of card */
  .card-front { left: 615px; background: var(--white); }
  .brand { position: absolute; left: 30px; top: 52px; width: 215px; text-align: center; }
  .brand-dot { width: 92px; height: 92px; border-radius: 50%; background: var(--red); margin: 0 auto 14px; }
  .brand-name {
    color: var(--red); font-weight: 800; font-size: 24px; line-height: 1.1; text-transform: uppercase;
  }
  .divider { position: absolute; left: 262px; top: 40px; width: 1px; height: 150px; background: var(--red); }
  .contact { position: absolute; left: 285px; top: 44px; }
  .person { font-weight: 800; font-size: 24px; text-transform: uppercase; letter-spacing: 0.5px; line-height: 1; }
  .person .first { color: var(--red); }
  .person .last { color: var(--ink); }
  .role { font-size: 13px; color: var(--ink); margin-top: 6px; }
  .contact-list { list-style: none; margin-top: 16px; font-size: 14px; color: var(--ink); }
  .contact-list li { display: flex; align-items: center; gap: 8px; margin-bottom: 6px; white-space: nowrap; }
  .icon { width: 22px; height: 22px; flex: none; }
  .band { position: absolute; left: 0; bottom: 0; width: 550px; height: 120px; }
</style>
</head>
<body>

<section class="card card-back">
  <div class="back-mark" role="img" aria-label="Faint embossed brand emblem area"></div>
  <ul class="extras">
    <li><span class="bullet"></span>Fencing</li>
    <li><span class="bullet"></span>Windows</li>
    <li><span class="bullet"></span>Gutters</li>
    <li><span class="bullet"></span>Siding</li>
    <li><span class="bullet"></span>Sheetrock</li>
    <li><span class="bullet"></span>Painting.</li>
  </ul>
  <ul class="services">
    <li><span class="bullet"></span>Residential &amp; Commercial Roofing</li>
    <li><span class="bullet"></span>Roof Repairs &amp; Maintenance</li>
    <li><span class="bullet"></span>Storm Damage &amp; Insurance Claims Specialist</li>
    <li><span class="bullet"></span>Christmas Lights and Permanent Christmas Lights</li>
  </ul>
</section>

<section class="card card-front">
  <div class="brand">
    <div class="brand-dot" aria-hidden="true"></div>
    <div class="brand-name">Copperleaf Roofing Co.</div>
  </div>
  <div class="divider"></div>
  <div class="contact">
    <div class="person"><span class="first">Dale</span> <span class="last">Mercer</span></div>
    <div class="role">OWNER</div>
    <ul class="contact-list">
      <li>
        <svg class="icon" viewBox="0 0 22 22"><circle cx="11" cy="11" r="11" fill="var(--red)"/><path d="M7.5 6.5c.6-.6 1.3-.5 1.7.1l1 1.4c.3.5.2 1-.2 1.4l-.6.6c.6 1.2 1.5 2.1 2.7 2.7l.6-.6c.4-.4.9-.5 1.4-.2l1.4 1c.6.4.7 1.1.1 1.7l-.7.7c-.9.9-3.4.1-5.5-2s-2.9-4.6-2-5.5z" fill="var(--white)"/></svg>
        555-014-2290
      </li>
      <li>
        <svg class="icon" viewBox="0 0 22 22"><circle cx="11" cy="11" r="11" fill="var(--red)"/><rect x="5.5" y="7" width="11" height="8" rx="1" fill="var(--white)"/><path d="M5.8 7.5l5.2 4 5.2-4" stroke="var(--red)" stroke-width="1.2" fill="none"/></svg>
        dale@copperleafroofing.co
      </li>
      <li>
        <svg class="icon" viewBox="0 0 22 22"><circle cx="11" cy="11" r="11" fill="var(--red)"/><g stroke="var(--white)" stroke-width="1.2" fill="none"><circle cx="11" cy="11" r="5.5"/><ellipse cx="11" cy="11" rx="2.4" ry="5.5"/><path d="M5.5 11h11M6.3 8.2h9.4M6.3 13.8h9.4"/></g></svg>
        www.copperleafroofing.co
      </li>
    </ul>
  </div>
  <svg class="band" viewBox="0 0 550 120" preserveAspectRatio="none" aria-hidden="true">
    <polygon points="0,120 550,20 550,120" fill="var(--red-dark)"/>
    <polygon points="0,120 550,40 550,120" fill="var(--red)"/>
    <polygon points="0,120 260,73 550,120" fill="var(--red-dark)" opacity="0.5"/>
    <line x1="0" y1="108" x2="550" y2="8" stroke="var(--red)" stroke-width="3"/>
    <circle cx="500" cy="30" r="27" fill="var(--white)" stroke="var(--red)" stroke-width="3"/>
  </svg>
</section>

</body>
</html>
```